landscaping core flute signs

I need core flutes created with business name and a few extra dot points for putting on fences for job sites 120cm x 120cm approx.
I want our old ones information with the new L logo and colour palette

```html
<!DOCTYPE html>
<html lang="en">
<head>
<meta charset="utf-8">
<title>Grounded Form – Site Sign</title>
<link href="https://fonts.googleapis.com/css2?family=Montserrat:wght@500;600;700&display=swap" rel="stylesheet">
<style>
  :root {
    --backdrop: #e9e9e9;
    --sign: #ffffff;
    --ink: #1a1a1a;
    --text: #2b2b2b;
    --green: #5f8c59;
  }
  * { margin: 0; padding: 0; box-sizing: border-box; }
  html, body { width: 1200px; height: 829px; overflow: hidden; background: var(--backdrop); }
  body { font-family: "Montserrat", Arial, sans-serif; position: relative; }

  .sign {
    position: absolute; left: 220px; top: 34px;
    width: 760px; height: 760px;
    background: var(--sign);
    overflow: hidden;
  }
  .brand-dot {
    position: absolute; left: 285px; top: 48px;
    width: 190px; height: 190px; border-radius: 50%;
    background: var(--green);
  }
  .brand-name {
    position: absolute; left: 0; width: 100%; text-align: center;
    color: var(--ink); font-weight: 600; line-height: 1;
  }
  .brand-name.primary { top: 258px; font-size: 54px; letter-spacing: 1px; }
  .brand-name.secondary { top: 322px; font-size: 26px; letter-spacing: 10px; padding-left: 10px; }
  .brand-rule {
    position: absolute; top: 335px; height: 2px; width: 92px; background: var(--ink);
  }
  .brand-rule.left { left: 190px; }
  .brand-rule.right { left: 478px; }
  .tagline {
    position: absolute; top: 358px; width: 100%; text-align: center;
    color: var(--green); font-size: 15px; font-weight: 500; letter-spacing: 4.5px;
  }
  .services { position: absolute; left: 187px; top: 388px; list-style: none; }
  .services li {
    display: flex; align-items: center; height: 59px;
    font-size: 29px; font-weight: 500; color: var(--text);
  }
  .services li::before {
    content: ""; width: 18px; height: 18px; border-radius: 50%;
    background: var(--green); margin-right: 14px;
  }
  .phone {
    position: absolute; top: 558px; width: 100%; text-align: center;
    font-size: 64px; font-weight: 700; color: var(--text); letter-spacing: 1px;
  }
  .email {
    position: absolute; top: 643px; width: 100%; text-align: center;
    font-size: 30px; font-weight: 600; color: var(--text);
  }
  .footer-band { position: absolute; left: 0; top: 710px; width: 760px; height: 50px; }
  .licence {
    position: absolute; right: 58px; top: 718px;
    color: #fff; font-size: 21px; font-weight: 700; letter-spacing: 0.5px;
  }
</style>
</head>
<body>
  <div class="sign">
    <div class="brand-dot"></div>
    <div class="brand-name primary">GROUNDED</div>
    <span class="brand-rule left"></span>
    <div class="brand-name secondary">FORM</div>
    <span class="brand-rule right"></span>
    <div class="tagline">STRUCTURAL LANDSCAPING</div>

    <ul class="services">
      <li>Paving &amp; Concreting</li>
      <li>Fencing &amp; Retaining</li>
      <li>Desgin &amp; Construct</li>
    </ul>

    <div class="phone">0400 123 987</div>
    <div class="email">sam@groundedform.com</div>

    <svg class="footer-band" viewBox="0 0 760 50" aria-hidden="true">
      <path d="M0 21 L470 21 C488 21 494 2 515 2 L760 2 L760 50 L0 50 Z" fill="var(--green)"/>
      <path d="M0 9 L462 9 C475 9 480 4 490 1" fill="none" stroke="var(--ink)" stroke-width="6"/>
    </svg>
    <div class="licence">QBSA:&nbsp; 1098342</div>
  </div>
</body>
</html>
```